Tallow Reed Software

We are a software company selling endpoint visibility, access and security technology to enterprise-level IT departments.

Our technology helps organizations gain comprehensive visibility into and control over devices accessing their corporate network so they can quickly identify and address suspicious activity on the network that could lead to potential threats like data breaches.

This technology can cost organizations upwards of $1M - depending on the size of the organization. Our primary clients are Pinnacle 2,000 companies.

We want a professional, polished business card to represent our new brand.

Info fields to include on the card:
Name
Job Title
Office Phone #
Cell Phone #
Email address
Address: 4270 Vestridge Pond Blvd., Ste. 2600, Bloomington, MN 55812
Website address: www.tallowreedsoftware.example
Tagline: Discover the edge. Optimize the whole.

Logo files and color specs document are attached. Would like color scheme to coordinate with the logo.

Also looking at stationary/envelope designs in conjunction with the business card designs. Received very few designs that included the stationary.

Software

```html
<!DOCTYPE html>
<html lang="en">
<head>
<meta charset="utf-8">
<title>Tallow Reed Software — Business Card</title>
<link href="https://fonts.googleapis.com/css2?family=PT+Sans:ital,wght@0,400;0,700;1,400&display=swap" rel="stylesheet">
<style>
  :root {
    --backdrop: #e6e6e4;
    --brand-red: #a83236;
    --card-white: #ffffff;
    --ink: #4a4a4a;
    --ink-soft: #5e5e5e;
    --on-red: #ffffff;
  }
  * { margin: 0; padding: 0; box-sizing: border-box; }
  html, body {
    width: 1200px;
    height: 1000px;
    overflow: hidden;
    background: var(--backdrop);
    font-family: "PT Sans", sans-serif;
  }
  .canvas {
    position: relative;
    width: 1200px;
    height: 1000px;
  }
  .card {
    position: absolute;
    top: 392px;
    width: 332px;
    height: 216px;
  }
  .card--front {
    left: 230px;
    background: var(--brand-red);
    display: flex;
    align-items: center;
    justify-content: center;
  }
  .front-brand {
    display: flex;
    align-items: center;
    gap: 10px;
  }
  .front-brand__square {
    width: 16px;
    height: 16px;
    background: var(--on-red);
    opacity: 1;
  }
  .front-brand__name {
    color: var(--on-red);
    font-weight: 700;
    font-size: 15px;
    letter-spacing: 1.5px;
    line-height: 1.1;
    text-transform: uppercase;
  }
  .card--back {
    left: 639px;
    width: 330px;
    background: var(--card-white);
  }
  .back-brand {
    position: absolute;
    top: 40px;
    right: 32px;
    color: var(--brand-red);
    font-weight: 700;
    font-size: 9px;
    letter-spacing: 1px;
    text-transform: uppercase;
  }
  .person {
    position: absolute;
    left: 33px;
    top: 90px;
  }
  .person__name {
    color: var(--ink);
    font-size: 19px;
    font-weight: 400;
    line-height: 1.1;
  }
  .person__title {
    color: var(--ink-soft);
    font-size: 11px;
    font-style: italic;
    margin-top: 2px;
  }
  .contact {
    position: absolute;
    left: 33px;
    top: 160px;
    color: var(--ink-soft);
    font-size: 8.6px;
    line-height: 12px;
    list-style: none;
  }
</style>
</head>
<body>
  <main class="canvas">
    <section class="card card--front" aria-label="Card front">
      <div class="front-brand">
        <span class="front-brand__square"></span>
        <span class="front-brand__name">Tallow Reed<br>Software</span>
      </div>
    </section>

    <section class="card card--back" aria-label="Card back">
      <div class="back-brand">Tallow Reed</div>
      <div class="person">
        <h1 class="person__name">Mara Ellison</h1>
        <p class="person__title">Managing Director</p>
      </div>
      <ul class="contact">
        <li>Office: 555-0142-3390 / Cell : 555-0142-3390</li>
        <li>contact@tallowreedsoftware.example / www.tallowreedsoftware.example</li>
        <li>4270 Vestridge Pond Blvd., Ste. 2600, Bloomington, MN 55812</li>
      </ul>
    </section>
  </main>
</body>
</html>
```